Penny Harvest

Logo and general packaging design for premium quality, price conscious super foods.

Initial product portfolio includes:

Organic Raw Chia Seeds - Resealable plastic bags with 3 x 5 label.
Organic Cold Pressed Coconut Oil (plastic jar) - 2.5 x 6.5 label

The design should be transferable to additional products.

Project requirements:

The design should be simple and the core trade dress should be no more than 2 or 3 colors. The logo should reproduce well in black/1 color.

The idea of this design is to convey quality and simplicity, like a "no frills", premium quality brand.

Deliverable: fully editable (text and illustration):

Logo.

Basic Jar label design.

Basic Bag label design.

Target Market(s)

Educated women aged 22-45

Industry/Entity Type

Plastic

Requirements
Must have
• Clear, simple logo, delivered in vector form, 1 color/black.
• Use of logo on 1 jar label and 1 bag label, each with product name and space for required and optional marketing content.
Nice to have
• Additional iterations of the design to demonstrate your concept of how we will visually vary additional items in jars and bags.
• i.e. What an additional product in a bag would look like for purposes of brand consistency and product differentiation on shelf or online in e-store.
Should not have
• overly detailed graphics that don't scale well and/or may be hard to read or understand. 4 color design elements (except to simiulate how the product may look through the clear jar or bag or how the product may be placed in a simulated surrounding or ad.

```html
<!DOCTYPE html>
<html lang="en">
<head>
<meta charset="utf-8">
<title>Penny Harvest – Organic Raw Chia Seeds Bag Label</title>
<link rel="stylesheet" href="https://fonts.googleapis.com/css2?family=PT+Sans+Narrow:wght@400;700&family=Open+Sans:wght@400&family=Arimo:wght@700&display=swap">
<style>
  :root {
    --backdrop: #e2e2e2;
    --pouch-green: #6f8b5f;
    --pouch-green-dark: #5f7a50;
    --window-edge: #9fb887;
    --harvest-yellow: #e6da8c;
    --gold: #ead98c;
    --sage-light: #c8dba6;
    --ink-green: #3f5a33;
    --earth-brown: #8a6a48;
    --seed-dark: #3b2a22;
    --seed-mid: #6a5140;
    --white: #ffffff;
  }
  * { margin: 0; padding: 0; box-sizing: border-box; }
  html, body { width: 1200px; height: 1200px; overflow: hidden; background: var(--backdrop); }
  .canvas { position: relative; width: 1200px; height: 1200px; }
  .pouch-art { position: absolute; inset: 0; }
  .brand-name {
    position: absolute; left: 0; width: 1200px; top: 298px; text-align: center;
    font-family: "PT Sans Narrow", sans-serif; font-weight: 400; font-size: 50px;
    color: var(--gold);
  }
  .product-descriptor {
    position: absolute; left: 0; width: 1200px; top: 358px; text-align: center;
    font-family: "PT Sans Narrow", sans-serif; font-weight: 400; font-size: 64px;
    color: var(--sage-light); -webkit-text-stroke: 1.5px var(--ink-green);
  }
  .product-name {
    position: absolute; left: 0; width: 1200px; top: 420px; text-align: center;
    font-family: "Open Sans", sans-serif; font-weight: 400; font-size: 96px;
    letter-spacing: -1px; color: var(--white); -webkit-text-stroke: 1.5px var(--ink-green);
  }
  .net-weight {
    position: absolute; left: 338px; top: 1055px;
    font-family: "Arimo", sans-serif; font-weight: 700; font-size: 46px;
    color: var(--ink-green);
  }
</style>
</head>
<body>
<main class="canvas">
  <svg class="pouch-art" width="1200" height="1200" viewBox="0 0 1200 1200" aria-hidden="false">
    <defs>
      <linearGradient id="seedTone" x1="0" y1="0" x2="1" y2="1">
        <stop offset="0" stop-color="var(--seed-mid)"/>
        <stop offset="1" stop-color="var(--seed-dark)"/>
      </linearGradient>
    </defs>
    <!-- pouch body -->
    <rect class="pouch-body" x="300" y="75" width="610" height="1065" fill="var(--pouch-green)"/>
    <rect class="pouch-top-band" x="300" y="75" width="610" height="50" fill="var(--pouch-green-dark)"/>
    <rect class="pouch-bottom-band" x="300" y="760" width="610" height="380" fill="var(--harvest-yellow)"/>

    <!-- product window -->
    <path class="window-frame" d="M378 1075 C350 820 520 590 892 508 C810 790 650 1010 378 1075 Z" fill="var(--window-edge)"/>
    <path class="product-window" role="img" aria-label="View of chia seeds through the clear window"
          d="M390 1060 C368 825 528 610 872 528 C795 790 640 995 390 1060 Z" fill="url(#seedTone)"/>

    <!-- decorative leaf motifs -->
    <g class="leaf-motif" role="img" aria-label="Decorative leaf motif" fill="var(--sage-light)" opacity="0.55">
      <ellipse cx="480" cy="155" rx="30" ry="20" transform="rotate(-30 480 155)"/>
    </g>
    <g class="leaf-motif" role="img" aria-label="Decorative leaf motif" fill="var(--sage-light)" opacity="0.55">
      <ellipse cx="810" cy="262" rx="42" ry="26" transform="rotate(-30 810 262)"/>
    </g>
    <g class="leaf-motif" role="img" aria-label="Decorative leaf motif" fill="var(--sage-light)" opacity="0.55">
      <ellipse cx="385" cy="605" rx="55" ry="40" transform="rotate(35 385 605)"/>
    </g>
    <g class="leaf-motif" role="img" aria-label="Decorative leaf motif" fill="var(--pouch-green)" opacity="0.8">
      <ellipse cx="760" cy="1010" rx="110" ry="45" transform="rotate(-20 760 1010)"/>
    </g>

    <!-- badges (plain shapes) -->
    <circle class="organic-badge" cx="400" cy="245" r="68" fill="none" stroke="var(--sage-light)" stroke-width="5" opacity="0.8"/>
    <polygon class="certification-badge" points="822,790 858,790 884,816 884,852 858,878 822,878 796,852 796,816"
             fill="none" stroke="var(--earth-brown)" stroke-width="5"/>

    <!-- brand mark placeholder -->
    <circle class="brand-dot" cx="600" cy="225" r="50" fill="var(--gold)"/>
  </svg>

  <p class="brand-name">Penny Harvest</p>
  <p class="product-descriptor">Organic Raw</p>
  <h1 class="product-name">Chia Seeds</h1>
  <p class="net-weight">e 200g</p>
</main>
</body>
</html>
```